Velvet Pressings Techno Label Business Card

I'm looking for a very clean business card for my Velvet Pressings music label. The label focusses on techno music. The card should include:

• my name : Tomas Brandt as "Founder & CEO"
• email address: tomas@velvet-pressings.example
• web: www.velvet-pressings.example
• facebook logo + /velvetpress
• twitter logo + /velvetpress
• soundcloud logo + /velvetpressings

Feel free to include your ideas! I'm looking forward to discuss about it.

Tomas

Industry/Entity Type

Business

Contact Information for Business Card

I don't like glossy cards. Prefer matt.

Requirements
Nice to have
• Maybe on one side the complete logo, other side just the icon.
Should not have
• Flashy stuff. Must be clean and business like style.

```html
<!DOCTYPE html>
<html lang="en">
<head>
<meta charset="utf-8">
<title>Velvet Pressings – Business Card</title>
<link href="https://fonts.googleapis.com/css2?family=Open+Sans:wght@400;600;700&display=swap" rel="stylesheet">
<style>
  :root {
    --backdrop: #e9e9e9;
    --brand-orange: #f36f1b;
    --deep-orange: #e8620f;
    --card-white: #fbfbfb;
    --ink-grey: #6e6e6e;
    --soft-grey: #8a8a8a;
    --band-grey: #a3a3a3;
  }
  * { margin: 0; padding: 0; box-sizing: border-box; }
  html, body {
    width: 1200px;
    height: 726px;
    overflow: hidden;
    background: var(--backdrop);
    font-family: "Open Sans", Arial, sans-serif;
  }
  .canvas {
    position: relative;
    width: 1200px;
    height: 726px;
    display: flex;
    align-items: center;
    justify-content: center;
    gap: 50px;
  }
  .card {
    position: relative;
    width: 530px;
    height: 303px;
    border-radius: 3px;
    overflow: hidden;
    box-shadow: 0 2px 6px rgba(0,0,0,0.12);
  }

  /* Front: brand side */
  .card-front {
    background: var(--brand-orange);
    display: flex;
    align-items: center;
    justify-content: center;
    gap: 18px;
  }
  .front-dot {
    width: 34px;
    height: 34px;
    border-radius: 50%;
    background: #ffffff;
  }
  .front-name {
    color: #ffffff;
    font-weight: 700;
    font-size: 38px;
    letter-spacing: -0.5px;
  }

  /* Back: contact side */
  .card-back {
    background: var(--card-white);
  }
  .brand-lockup {
    position: absolute;
    left: 38px;
    top: 84px;
    display: flex;
    align-items: center;
    gap: 12px;
  }
  .brand-dot {
    width: 36px;
    height: 36px;
    border-radius: 50%;
    background: var(--brand-orange);
  }
  .brand-name {
    color: var(--ink-grey);
    font-weight: 700;
    font-size: 27px;
    line-height: 1.0;
    letter-spacing: -0.3px;
  }
  .person {
    position: absolute;
    left: 296px;
    top: 66px;
  }
  .person-name {
    color: var(--brand-orange);
    font-size: 17px;
    font-weight: 400;
    line-height: 1.2;
  }
  .person-role {
    color: var(--soft-grey);
    font-size: 10px;
    margin-top: 2px;
  }
  .contact-list {
    position: absolute;
    left: 296px;
    top: 122px;
    list-style: none;
  }
  .contact-item {
    display: flex;
    align-items: center;
    gap: 8px;
    color: var(--ink-grey);
    font-size: 11px;
    line-height: 17px;
    white-space: nowrap;
  }
  .contact-icon { width: 11px; height: 11px; flex: none; }
  .social-dot {
    width: 11px;
    height: 11px;
    border-radius: 50%;
    background: var(--brand-orange);
    flex: none;
  }
  .swoosh {
    position: absolute;
    left: 0;
    bottom: 0;
    width: 530px;
    height: 110px;
  }
</style>
</head>
<body>
  <main class="canvas">
    <section class="card card-front" aria-label="Card front">
      <span class="front-dot"></span>
      <span class="front-name">Velvet Pressings</span>
    </section>

    <section class="card card-back" aria-label="Card back">
      <div class="brand-lockup">
        <span class="brand-dot"></span>
        <span class="brand-name">Velvet<br>Pressings</span>
      </div>

      <div class="person">
        <p class="person-name">Tomas Brandt</p>
        <p class="person-role">Founder &amp; CEO</p>
      </div>

      <ul class="contact-list">
        <li class="contact-item">
          <svg class="contact-icon" viewBox="0 0 12 12" aria-hidden="true">
            <rect x="0.5" y="2" width="11" height="8" fill="var(--brand-orange)"/>
            <path d="M0.5 2 L6 6.5 L11.5 2" fill="none" stroke="#ffffff" stroke-width="1"/>
          </svg>
          tomas@velvet-pressings.example
        </li>
        <li class="contact-item">
          <svg class="contact-icon" viewBox="0 0 12 12" aria-hidden="true">
            <circle cx="6" cy="6" r="5.5" fill="var(--brand-orange)"/>
            <path d="M0.5 6 H11.5 M6 0.5 V11.5 M2 3.5 H10 M2 8.5 H10" stroke="#ffffff" stroke-width="0.8" fill="none"/>
          </svg>
          www.velvet-pressings.example
        </li>
        <li class="contact-item"><span class="social-dot" aria-hidden="true"></span>/velvetpress</li>
        <li class="contact-item"><span class="social-dot" aria-hidden="true"></span>/velvetpress</li>
        <li class="contact-item"><span class="social-dot" aria-hidden="true"></span>/velvetpressings</li>
      </ul>

      <svg class="swoosh" viewBox="0 0 530 110" preserveAspectRatio="none" aria-hidden="true">
        <path d="M0 110 L0 72 C140 112 330 80 530 34 L530 110 Z" fill="var(--band-grey)"/>
        <path d="M0 110 L0 86 C160 118 350 88 530 46 L530 110 Z" fill="var(--brand-orange)"/>
        <path d="M0 110 L0 100 C170 122 360 96 530 64 L530 110 Z" fill="var(--deep-orange)"/>
      </svg>
    </section>
  </main>
</body>
</html>
```